Etiketten für Imkerei mit Spezialisierung auf Bio Lagenhonig
Zielgruppe
wiesfalter.at - BioImkerei Lindorf
Kleine Nebenerwerbs Imkerei mit Spezialisierung auf Bio Lagenhonig (nähere Infos sind auf der Website nachzulesen)
Als weitere Produktlinie bieten wir Honig+ / Honig mit Zutaten wie Himbeer, Erdbeer, Haselnuss, Mohn, Ingwer, Thymian, usw an.
Zielgruppe: Personen die offen für die Vielfalt der Natur sind, gesunde und natürliche Lebensmittel lieben und die bereit sind die aufwändige, großteils manuelle, Arbeit entsprechend zu entlohnen.
Gesucht:
ÄNDERUNG: Da die Anforderung für das ausgesetzte Preisgeld offensichtlich zu komplex ist, reduziere ich die Anforderung auf Etiketten für die Produktserie Honig+, Gesamtkonzepte sind nicht erforderlich werden aber gerne angenommen.
ÜRSPRÜNGLICH:
Redesign der aktuellen Honigetiketten
Basisdesign für Lagenhonig und Honig+ das entsprechende Varianten zulässt.
Aufgabenstellung
Ich wünsche mir ein modernes, edles (oder Öko look) Design mit sehr guten Wiedererkennungswert das sich von gängigen Honigetiketten deutlich abhebt.
Das wiesfalter Logo soll enthalten sein kann aber bei Bedarf angepasst werden (z.B. monocrome Verison)
Für Lagenhonig werden derzeit 400g und 100g Gläser mit hohem schwarzen DrehKap Decke und,
für Honig+ 250g und 100g mit hohem silbenen DrehKap Deckel verwendet. Beispiele sind im Webshop unter https://solvenhof.at/index.php/wiesfalter ersichtilich.
Für das Ablaufdatum ist evtl. ein Feld für manuelle Stempelung vorzusehen.
Bitte die Sichtfeldregelung der EU Verpackungsverordnung einhalten.
Bisherige Etiketten hatten den Anspruch das diese auf guten Laserdruckern ausdruckbar waren - das ist jetzt nicht mehr zwingend notwendig (wäre für Kleinauflagen aber trotzdem vorteilhaft)

```html
<!DOCTYPE html>
<html lang="de">
<head>
<meta charset="utf-8">
<title>wiesfalter – honig + Erdbeere</title>
<link href="https://fonts.googleapis.com/css2?family=Roboto:wght@300;400&display=swap" rel="stylesheet">
<style>
  :root {
    --page: #ffffff;
    --label: #0b0b0b;
    --line: #ffffff;
    --text: #ffffff;
    --accent: #f5a623;
    --berry: #f0606a;
  }
  html, body {
    margin: 0;
    padding: 0;
    width: 1200px;
    height: 1200px;
    overflow: hidden;
    background: var(--page);
  }
  .canvas {
    position: relative;
    width: 1200px;
    height: 1200px;
    font-family: "Roboto", Arial, sans-serif;
  }
  .label {
    position: absolute;
    left: 50px;
    top: 298px;
    width: 1100px;
    height: 604px;
    background: var(--label);
    color: var(--text);
  }
  .brand {
    position: absolute;
    left: 0;
    right: 0;
    top: 70px;
    display: flex;
    align-items: center;
    justify-content: center;
    gap: 14px;
    font-size: 30px;
    font-weight: 400;
    letter-spacing: 0.04em;
    color: var(--accent);
  }
  .brand-dot {
    width: 18px;
    height: 18px;
    border-radius: 50%;
    background: var(--accent);
  }
  .product-table {
    position: absolute;
    left: 186px;
    top: 274px;
    width: 711px;
    height: 244px;
    box-sizing: border-box;
    border: 3px solid var(--line);
    border-left: none;
  }
  .row {
    position: absolute;
    left: 0;
    right: 0;
    height: 50%;
    display: flex;
  }
  .row-top { top: 0; border-bottom: 3px solid var(--line); box-sizing: border-box; }
  .row-bottom { bottom: 0; }
  .cell {
    display: flex;
    align-items: center;
    box-sizing: border-box;
    padding-left: 16px;
    font-size: 44px;
    font-weight: 300;
    white-space: nowrap;
  }
  .cell-line { width: 320px; }
  .cell-flavour-pattern {
    flex: 1;
    padding: 10px 0 10px 0;
  }
  .berry-pattern {
    width: 100%;
    height: 100%;
    background: var(--berry);
  }
  .cell-weight {
    width: 192px;
    border-left: 3px solid var(--line);
    border-right: 3px solid var(--line);
  }
  .cell-weight:first-child { border-left: 3px solid var(--line); }
  .row-top .cell-line { border-left: 3px solid var(--line); }
  .cell-name { flex: 1; padding-left: 20px; }
</style>
</head>
<body>
  <div class="canvas">
    <section class="label">
      <div class="brand">
        <span class="brand-dot"></span>
        <span class="brand-name">wiesfalter</span>
      </div>
      <div class="product-table">
        <div class="row row-top">
          <div class="cell cell-line">honig +</div>
          <div class="cell cell-flavour-pattern">
            <div class="berry-pattern" role="img" aria-label="Rotes Wabenmuster als Farbkennung für Erdbeere"></div>
          </div>
        </div>
        <div class="row row-bottom">
          <div class="cell cell-weight">100 g</div>
          <div class="cell cell-name">Erdbeere in Bio Honig</div>
        </div>
      </div>
    </section>
  </div>
</body>
</html>
```